Boundless Volt Product design

We need a bottle design for our product. Boundless Volt is a Gaming Nootropic made to increase Energy, Focus, Reaction time, and Clarity of an eSport gamer. It will be 40 servings a bottle. Currently, all the ingredients haven't been finalized so after the competition is over we will have to work with the designer to also make an ingredients label for the back of it. For the flavor, we will call it tundra mist.

The attachments included:. The velvet outlaws picture as a font style I like for the logo.
The Z CHARGE REFRESH PICTURE IS WHAT WE WANT OUR DESIGN to look like something similar a clean and simple design that stands out!

Z Charge bottle is what our biggest competitors product looks like. The boundless volt picture as the current logo we are using but can be changed.

Overall the pictures are just some references for what I could possibly want the design to look like however, I'm open to your designer's ideas and concepts you think would make for a cool looking Gaming Nootropic product bottle design. I appreciate everyone working on this and look forward to seeing your designs have a great day!

Target Market(s)

Gamers between the ages of 18-30

Industry/Entity Type

Health And Wellness

Requirements
Must have
• Boundless Volt logo, state that it is for energy, focus, reaction, and clarity. state 40 serivngs. state flavor.

```html
<!DOCTYPE html>
<html lang="en">
<head>
<meta charset="utf-8">
<title>Boundless Volt – Tundra Mist Label</title>
<link rel="stylesheet" href="https://fonts.googleapis.com/css2?family=Oswald:wght@500;600&display=swap">
<style>
  :root {
    --canvas-bg: #333333;
    --brand-white: #ffffff;
    --label-blue: #3a8fcb;
    --label-blue-deep: #2f7fb8;
    --sky-top: #8fd0f3;
    --sky-glow: #eaf7fe;
    --snow: #f4fbff;
    --ice: #5cbbe8;
  }
  * { margin: 0; padding: 0; box-sizing: border-box; }
  html, body {
    width: 1200px;
    height: 1200px;
    overflow: hidden;
    background: var(--canvas-bg);
  }
  .canvas {
    position: relative;
    width: 1200px;
    height: 1200px;
    background: var(--canvas-bg);
    font-family: "Oswald", "Arial Narrow", sans-serif;
  }

  /* Brand lockup on dark field */
  .brand-lockup {
    position: absolute;
    top: 517px;
    left: 408px;
    height: 60px;
    display: flex;
    align-items: center;
    gap: 24px;
  }
  .brand-lockup .brand-dot {
    width: 60px;
    height: 60px;
    border-radius: 50%;
    background: var(--brand-white);
  }
  .brand-lockup .brand-name {
    color: var(--brand-white);
    font-weight: 600;
    font-size: 46px;
    letter-spacing: 1px;
    line-height: 1;
    text-transform: uppercase;
  }

  /* Bottle wrap label */
  .bottle-label {
    position: absolute;
    left: 66px;
    top: 840px;
    width: 1068px;
    height: 298px;
    overflow: hidden;
  }
  .label-scene {
    position: absolute;
    inset: 0;
    background:
      radial-gradient(ellipse 260px 200px at 50% 10%, var(--sky-glow) 0%, rgba(234,247,254,0) 100%),
      linear-gradient(180deg, var(--sky-top) 0%, #b8e3f8 55%, var(--snow) 72%, #cfeefc 86%, var(--ice) 100%);
  }
  .label-content {
    position: absolute;
    inset: 0;
    display: flex;
    flex-direction: column;
    align-items: center;
    text-align: center;
  }
  .label-brand {
    margin-top: 44px;
    display: flex;
    align-items: center;
    gap: 14px;
  }
  .label-brand .brand-dot {
    width: 62px;
    height: 62px;
    border-radius: 50%;
    background: var(--label-blue);
  }
  .label-brand .brand-name {
    color: var(--label-blue);
    font-weight: 600;
    font-size: 24px;
    letter-spacing: 1px;
    text-transform: uppercase;
  }
  .flavor-name {
    margin-top: 16px;
    color: var(--label-blue);
    font-weight: 600;
    font-size: 56px;
    line-height: 1;
    letter-spacing: 1px;
    text-transform: uppercase;
  }
  .benefits {
    margin-top: 12px;
    display: flex;
    gap: 12px;
    color: var(--label-blue);
    font-weight: 600;
    font-size: 19px;
    line-height: 1;
    text-transform: uppercase;
  }
  .servings {
    margin-top: 30px;
    color: var(--label-blue-deep);
    font-weight: 500;
    font-size: 17px;
    line-height: 1;
  }
</style>
</head>
<body>
<main class="canvas">
  <div class="brand-lockup">
    <span class="brand-dot"></span>
    <span class="brand-name">Boundless Volt</span>
  </div>

  <section class="bottle-label">
    <div class="label-scene" role="img" aria-label="Illustration of snowy glacier mountain peaks under a bright icy blue sky with a sun flare"></div>
    <div class="label-content">
      <div class="label-brand">
        <span class="brand-dot"></span>
        <span class="brand-name">Boundless Volt</span>
      </div>
      <h1 class="flavor-name">Tundra Mist</h1>
      <p class="benefits">
        <span>Energy</span><span>Focus</span><span>Reaction</span><span>Clarity</span>
      </p>
      <p class="servings">40 serivngs</p>
    </div>
  </section>
</main>
</body>
</html>
```